Simple Logo Design for Semi-Clear Plastic Frosted Card stock

Create a business card on frosted plastic. compliment existing logo elements with a tree trunk, roots, or seed at the lower half and the full logo both on the front.

Contact information will go on a solid portion of the back of this design since this card stock is semi-transparent.

It is important to consider this plastic card stock medium in your design. I found helpful tips and guides listed at vellaprint-sample.net: be careful to understand ink printed on plastic cards cannot have too much of a consistent print area or risks peeling and fine lines can easily scratch off.
Updates

2" x 3.5" 20PT Clear Plastic Business cards with Round corners Please get info or templates here: https://www.vellaprint-sample.net/product-detail/2-x-35-20pt-clear-plastic-business-cards-with-round-corners

Target Market(s)

Not for profit- religion

Industry/Entity Type

Business

Must include complementary elements to the existing logo

Font styles to use
Decorative

Colors
000000

Requirements
Must have
• Elements of community, nature and oneness. Such as: seed, roots, tree trunk, etc.
• Three lines of space on the back for Name, Title, Phone Number.
Nice to have
• I like a light use of decorative elements
Should not have
• No eyes, from faces or animals.

```html
<!DOCTYPE html>
<html lang="en">
<head>
<meta charset="utf-8">
<title>Steadfast Grove – Business Cards</title>
<link href="https://fonts.googleapis.com/css2?family=Cinzel:wght@400;700&family=Questrial&display=swap" rel="stylesheet">
<style>
  :root {
    --page-bg: #dfe4e8;
    --frost: rgba(255, 255, 255, 0.62);
    --frost-edge: rgba(255, 255, 255, 0.9);
    --forest: #2c5a3c;
    --forest-deep: #1f4a3e;
    --leaf: #5b9a3c;
    --teal-card: #2f5f56;
    --ink-grey: #5c6670;
    --pale: #e6ecec;
    --pale-green: #b9d6a8;
  }
  * { margin: 0; padding: 0; box-sizing: border-box; }
  html, body { width: 800px; height: 1200px; overflow: hidden; }
  body { background: var(--page-bg); position: relative; font-family: "Questrial", sans-serif; }

  .card {
    position: absolute; left: 100px; width: 600px; height: 343px;
    border-radius: 16px; overflow: hidden;
    box-shadow: 0 10px 30px rgba(30, 45, 55, 0.18);
  }
  .card-contact { top: 140px; background: var(--frost); border: 1px solid var(--frost-edge); }
  .card-brand { top: 700px; background: var(--teal-card); }
  .card-shapes { position: absolute; inset: 0; width: 100%; height: 100%; }

  /* Contact side */
  .brand-mark-small {
    position: absolute; left: 118px; top: 34px; width: 74px; height: 74px;
    border-radius: 50%; background: var(--forest);
  }
  .wordmark-small {
    position: absolute; left: 26px; top: 114px;
    font-size: 31px; letter-spacing: 1px; color: var(--ink-grey); white-space: nowrap;
  }
  .tagline-small {
    position: absolute; left: 48px; top: 152px;
    font-size: 10.5px; letter-spacing: 0.8px; color: var(--forest);
    text-transform: uppercase; white-space: nowrap;
  }
  .person-name {
    position: absolute; right: 28px; top: 190px;
    font-family: "Cinzel", serif; font-weight: 700; font-size: 20px; color: var(--forest-deep);
  }
  .divider { position: absolute; left: 0; right: 22px; top: 224px; height: 1px; background: var(--forest-deep); }
  .person-title {
    position: absolute; right: 28px; top: 229px;
    font-family: "Cinzel", serif; font-size: 11px; color: var(--forest-deep);
  }
  .contact-list { position: absolute; left: 30px; top: 272px; list-style: none; }
  .contact-list li {
    display: flex; align-items: center; gap: 8px; height: 22px;
    font-family: "Cinzel", serif; font-size: 11px; color: var(--forest-deep);
  }
  .contact-list svg { width: 11px; height: 11px; fill: var(--forest-deep); }

  /* Brand side */
  .brand-mark-large {
    position: absolute; left: 258px; top: 60px; width: 84px; height: 84px;
    border-radius: 50%; background: var(--pale);
  }
  .wordmark-large {
    position: absolute; left: 0; right: 0; top: 160px; text-align: center;
    font-size: 38px; letter-spacing: 1.5px; color: var(--pale); white-space: nowrap;
  }
  .tagline-large {
    position: absolute; left: 0; right: 0; top: 207px; text-align: center;
    font-size: 13px; letter-spacing: 1px; color: var(--pale-green);
    text-transform: uppercase; white-space: nowrap;
  }
</style>
</head>
<body>

<section class="card card-contact" aria-label="Contact side">
  <svg class="card-shapes" viewBox="0 0 600 343" aria-hidden="true">
    <rect x="0" y="334" width="600" height="9" fill="#3f7a3a"/>
    <path d="M340 343 C350 318 368 311 392 311 L600 311 L600 343 Z" fill="#24493a"/>
  </svg>
  <div class="brand-mark-small" aria-hidden="true"></div>
  <div class="wordmark-small">STEADFASTGROVE</div>
  <div class="tagline-small">Growth, Fellowship &amp; Stillness</div>
  <div class="person-name">DANA WHITFIELD</div>
  <div class="divider"></div>
  <div class="person-title">Director</div>
  <ul class="contact-list">
    <li><svg viewBox="0 0 24 24"><path d="M6.6 10.8a15.1 15.1 0 0 0 6.6 6.6l2.2-2.2a1 1 0 0 1 1-.25 11.4 11.4 0 0 0 3.6.57 1 1 0 0 1 1 1V20a1 1 0 0 1-1 1A17 17 0 0 1 3 4a1 1 0 0 1 1-1h3.5a1 1 0 0 1 1 1c0 1.25.2 2.45.57 3.6a1 1 0 0 1-.25 1z"/></svg>+330 2555-0142</li>
    <li><svg viewBox="0 0 24 24"><path d="M2 5h20v14H2z M4 7l8 6 8-6" fill="none" stroke="#1f4a3e" stroke-width="2"/></svg>dana@whitfieldgrove.com</li>
  </ul>
</section>

<section class="card card-brand" aria-label="Brand side">
  <svg class="card-shapes" viewBox="0 0 600 343" aria-hidden="true">
    <path d="M0 306 L220 306 C244 306 258 316 266 334 L266 343 L0 343 Z" fill="#3d7a46"/>
    <rect x="266" y="334" width="334" height="9" fill="#cfdad6"/>
  </svg>
  <div class="brand-mark-large" aria-hidden="true"></div>
  <div class="wordmark-large">STEADFASTGROVE</div>
  <div class="tagline-large">Growth, Fellowship &amp; Stillness</div>
</section>

</body>
</html>
```